IT support company needs Banner Ad for the top of their quote layout template

We need a banner Ad for the top of our for quote layout template so it is sent out on all our quotes

The banner size must be 827 x 100 pixels - anything larger than 60 KB can cause upload time issues

We have attached our logo and examples of the quote page to see how it looks in the context of the whole page.

Essential elements of the banner
- Must have our logo but this can be changed to be different colours if it makes the design work better i.e. Kelmor Wave could be all in white

Colours
- Can use all of our standard colours - Orange, Black, Grey and White

Images
- As a premium IT support company we deal with people and technology so would like to see both of these Incorporated into the banner i.e. people using technology These images could be watermarked or one colour effect.

Look and Feel
- Professional, friendly, people, technology, premium

Target Market
Small business owners and managers

Industry/Entity Type

It Company

```html
<!DOCTYPE html>
<html lang="en">
<head>
<meta charset="utf-8">
<title>Kelmor Wave – Quote Header Banner</title>
<link rel="stylesheet" href="https://fonts.googleapis.com/css2?family=Orbitron:wght@500;800&family=Michroma&display=swap">
<style>
  :root {
    --backdrop: #6b6b6b;
    --brand-orange: #e35817;
    --orange-soft: #ec8a55;
    --peach: #f6cfb4;
    --white: #ffffff;
    --ink-grey: #3a3a3a;
  }
  html, body {
    margin: 0;
    padding: 0;
    width: 1200px;
    height: 1200px;
    overflow: hidden;
    background: var(--backdrop);
  }
  .banner {
    position: absolute;
    left: 35px;
    top: 533px;
    width: 1129px;
    height: 136px;
    overflow: hidden;
    background: linear-gradient(90deg,
      var(--brand-orange) 0%,
      var(--brand-orange) 30%,
      var(--orange-soft) 42%,
      var(--peach) 52%,
      var(--white) 68%,
      var(--white) 100%);
  }
  .banner__texture {
    position: absolute;
    left: 420px;
    top: 0;
    width: 709px;
    height: 136px;
  }
  .brand-name {
    position: absolute;
    left: 42px;
    top: 46px;
    margin: 0;
    font-family: "Orbitron", sans-serif;
    font-weight: 500;
    font-size: 36px;
    letter-spacing: 0.5px;
    color: var(--white);
    white-space: nowrap;
  }
  .headline-block {
    position: absolute;
    right: 158px;
    top: 30px;
    text-align: right;
  }
  .headline {
    margin: 0;
    font-family: "Orbitron", sans-serif;
    font-weight: 800;
    font-size: 27px;
    line-height: 31px;
    letter-spacing: 0.5px;
    color: var(--brand-orange);
    white-space: nowrap;
  }
  .tagline {
    margin: 6px 0 0;
    font-family: "Michroma", sans-serif;
    font-size: 13.5px;
    color: var(--ink-grey);
    white-space: nowrap;
  }
</style>
</head>
<body>
  <section class="banner">
    <svg class="banner__texture" viewBox="0 0 709 136" role="img" aria-label="Soft orange and white abstract technology texture of crossing light beams">
      <defs>
        <linearGradient id="textureTone" x1="0" y1="0" x2="1" y2="0">
          <stop offset="0" stop-color="#f3b48c" stop-opacity="0"/>
          <stop offset="0.25" stop-color="#f3b48c" stop-opacity="0.45"/>
          <stop offset="0.5" stop-color="#ffffff" stop-opacity="0"/>
          <stop offset="0.82" stop-color="#ffffff" stop-opacity="0"/>
          <stop offset="1" stop-color="#f0a678" stop-opacity="0.55"/>
        </linearGradient>
      </defs>
      <rect width="709" height="136" fill="url(#textureTone)"/>
    </svg>

    <p class="brand-name">Kelmor Wave</p>

    <div class="headline-block">
      <h1 class="headline">LOREM IPSUM<br>DOLOR SIT AMET</h1>
      <p class="tagline">consectetuer adipiscing elit</p>
    </div>
  </section>
</body>
</html>
```